RTavenor Business Cards & Letterhead

I have a logo but need a design for some new business cards. We are a Design-Build Firm that specializes in the design and construction of commercial projects.
the cards need to be professional. no cartoon stuff.
i would like to have the cards in AI format so I can update the card as needed. Logo is provided.
Our Address is: 4187 Marlowe Ct. Cedar Bluff, Oregon 27614

```html
<!DOCTYPE html>
<html lang="en">
<head>
<meta charset="utf-8">
<title>RTavenor Business Card</title>
<link href="https://fonts.googleapis.com/css2?family=Montserrat:wght@400;500;700;800&display=swap" rel="stylesheet">
<style>
  :root {
    --backdrop: #c9c9c9;
    --card-white: #ffffff;
    --card-dark: #222222;
    --brand-blue: #1b74bb;
    --ink-dark: #1d2733;
    --ink-light: #ffffff;
  }
  * { box-sizing: border-box; margin: 0; padding: 0; }
  html, body { width: 1200px; height: 815px; overflow: hidden; }
  body {
    background: linear-gradient(180deg, #d3d3d3 0%, var(--backdrop) 60%, #b9b9b9 100%);
    font-family: "Montserrat", sans-serif;
    position: relative;
  }
  .card {
    position: absolute;
    width: 540px;
    height: 310px;
    border-radius: 18px;
    overflow: hidden;
    box-shadow: 0 14px 30px rgba(0,0,0,0.25);
    top: 252px;
  }
  .card-front { left: 40px; background: var(--card-dark); }
  .card-back { left: 620px; background: var(--card-dark); }

  .front-top {
    position: absolute; left: 0; top: 0; width: 100%; height: 176px;
    background: var(--card-white);
  }
  .front-rule {
    position: absolute; left: 0; top: 180px; width: 100%; height: 5px;
    background: var(--brand-blue);
  }
  .name-marker {
    position: absolute; left: 0; top: 104px; width: 14px; height: 40px;
    background: var(--brand-blue);
  }
  .person { position: absolute; left: 34px; top: 104px; }
  .person-name {
    font-weight: 700; font-size: 24px; letter-spacing: 1px;
    color: var(--brand-blue); line-height: 1;
  }
  .person-title {
    font-weight: 400; font-size: 14px; letter-spacing: 1px;
    color: var(--ink-dark); margin-top: 4px;
  }
  .front-brand {
    position: absolute; right: 40px; top: 64px;
    font-weight: 800; font-size: 32px; letter-spacing: 1px;
    color: var(--ink-dark);
  }
  .reg { font-size: 10px; vertical-align: top; font-weight: 700; }

  .contacts {
    position: absolute; left: 34px; top: 218px;
    list-style: none; color: var(--ink-light);
    font-size: 13px; line-height: 24px;
  }
  .contacts li { display: flex; align-items: center; gap: 10px; }
  .contacts svg { width: 13px; height: 13px; fill: var(--brand-blue); flex: none; }

  .address {
    position: absolute; right: 34px; top: 224px;
    text-align: right; color: var(--ink-light);
    font-size: 13px; line-height: 22px; font-style: normal;
  }

  .back-brand {
    position: absolute; right: 40px; bottom: 52px;
    font-weight: 800; font-size: 42px; letter-spacing: 1px;
    color: var(--ink-light);
  }
  .back-brand .reg { font-size: 12px; }
</style>
</head>
<body>

  <section class="card card-front" aria-label="Business card front">
    <div class="front-top"></div>
    <div class="front-rule"></div>
    <div class="name-marker"></div>
    <div class="person">
      <p class="person-name">ELIAS VARDEN</p>
      <p class="person-title">MANAGER</p>
    </div>
    <p class="front-brand">RTAVENOR<span class="reg">®</span></p>

    <ul class="contacts">
      <li>
        <svg viewBox="0 0 24 24" aria-hidden="true"><path d="M6.6 10.8a15.1 15.1 0 0 0 6.6 6.6l2.2-2.2a1 1 0 0 1 1-.25 11.4 11.4 0 0 0 3.6.57 1 1 0 0 1 1 1V20a1 1 0 0 1-1 1A17 17 0 0 1 3 4a1 1 0 0 1 1-1h3.5a1 1 0 0 1 1 1c0 1.25.2 2.45.57 3.57a1 1 0 0 1-.25 1z"/></svg>
        555-204-3187
      </li>
      <li>
        <svg viewBox="0 0 24 24" aria-hidden="true"><path d="M2 5h20v14H2z M2 5l10 8 10-8" stroke="#222" stroke-width="1.5"/></svg>
        hello@rtavenorbuild.com
      </li>
      <li>
        <svg viewBox="0 0 24 24" aria-hidden="true"><circle cx="12" cy="12" r="10"/><path d="M2 12h20M12 2c3 3 3 17 0 20M12 2c-3 3-3 17 0 20" stroke="#222" stroke-width="1.3" fill="none"/></svg>
        www.rtavenorbuild.com
      </li>
    </ul>

    <address class="address">
      4187 Marlowe Ct.<br>
      Cedar Bluff, Oregon 27614
    </address>
  </section>

  <section class="card card-back" aria-label="Business card back">
    <p class="back-brand">RTAVENOR<span class="reg">®</span></p>
  </section>

</body>
</html>
```